Yacht, Boats, Watersports company needs a redesign of business card

Hello Designers!
We are a Boat dealership company that sells fun in the water, we sell boats, Yachts, Kayaks and also yacht WaterSport toys. We are looking to redesign our business cards in to something a little bit more sophisticated. in a way that we can make better use of our company colors. I'm attaching a zipped file containing the company 3 sets of company logo which one is an horizontal another one is a vertical and also a chromed 3d logo. Also is included two set of business cards that we use and also some designs that i think it's interesting. We use PMS 2026c Orange and PMS 7687C Blue. I would like to see at least two different options with the orange as accent and also using blue as an accent color. It's really important for the business cards to have a font option and size that is legible to most people. Our current website is wwww.coralpennant.com. Please visit if you want to have a better feeling of the Boat dealership
You can send Single sided or double side options. We are now using single sided but we may be open for a double side option if we really like the design.
Target Market(s)
Marine, boat sales, yacht sales, water toys sales/
Contact Information for Business Card
Name: Dale Whitcombe
Address: 212 North Fenwick Lane,
Seabrook Cove, FL 34112
Phone: 954-731-8842
Fax: 954:731-8843
Cell: 954-382-1490
Email: dw@coralpennant.com
Website: coralpennant.com
Requirements
Must have
- the current information of the business card provided.
logo
use the PMS Colors
Nice to have
- a touch of elegance and sophistication but simple
Should not have
- should not have any typography that is hard to read, the card should be simple but yet sophisticated.

```html
<!DOCTYPE html>
<html lang="en">
<head>
<meta charset="utf-8">
<title>Coral Pennant — Business Card</title>
<link rel="stylesheet" href="https://fonts.googleapis.com/css2?family=Roboto:wght@400;500;700&family=Roboto+Condensed:wght@700&display=swap">
<style>
  :root {
    --navy: #0f4475;
    --orange: #ee5a2b;
    --paper: #f4f4f4;
    --ink: #2a2a2a;
    --stage-light: #ececec;
    --stage-dark: #d9d9d9;
    --white: #ffffff;
  }
  * { margin: 0; padding: 0; box-sizing: border-box; }
  html, body { width: 1200px; height: 960px; overflow: hidden; }
  body {
    position: relative;
    background: radial-gradient(ellipse at 50% 50%, var(--stage-light) 0%, var(--stage-light) 40%, var(--stage-dark) 100%);
    font-family: "Roboto", Arial, sans-serif;
  }
  .card {
    position: absolute;
    left: 296px;
    width: 607px;
    height: 345px;
    box-shadow: 3px 4px 6px rgba(0,0,0,0.35);
    overflow: hidden;
  }
  .card--front { top: 110px; background: var(--navy); }
  .card--back { top: 509px; background: var(--paper); }

  .brand-dot {
    position: absolute;
    border-radius: 50%;
  }
  .card--front .brand-dot {
    left: 254px; top: 82px; width: 100px; height: 100px;
    border: 6px solid var(--orange);
  }
  .brand-name {
    position: absolute;
    left: 0; width: 100%;
    text-align: center;
    font-weight: 700;
    text-transform: uppercase;
    line-height: 1;
    white-space: nowrap;
  }
  .card--front .brand-name {
    top: 206px; font-size: 31px; letter-spacing: 11px; padding-left: 11px;
    color: var(--white);
  }
  .website {
    position: absolute;
    top: 292px; left: 0; width: 100%;
    text-align: center;
    font-size: 16px;
    letter-spacing: 1.6px;
    color: var(--white);
  }
  .website__domain { color: var(--orange); }

  .back-band {
    position: absolute; left: 0; top: 0;
    width: 100%; height: 76px;
    background: var(--navy);
    border-bottom: 2px solid var(--orange);
  }
  .card--back .brand-dot {
    left: 258px; top: 32px; width: 90px; height: 90px;
    background: var(--white);
    border: 6px solid var(--navy);
    box-shadow: 0 0 0 3px var(--white);
  }
  .card--back .brand-name {
    top: 137px; font-size: 25px; letter-spacing: 9px; padding-left: 9px;
    color: var(--navy);
  }

  .holder-name {
    position: absolute;
    right: 325px; top: 229px;
    font-family: "Roboto Condensed", "Roboto", Arial, sans-serif;
    font-weight: 700;
    font-size: 29px;
    color: var(--navy);
    white-space: nowrap;
  }
  .divider {
    position: absolute;
    left: 302px; top: 204px;
    width: 2px; height: 80px;
    background: var(--ink);
  }
  .contact-list {
    position: absolute;
    left: 321px; top: 202px;
    list-style: none;
  }
  .contact-list li {
    display: flex; align-items: center;
    height: 20.4px;
    font-size: 16px;
    color: var(--ink);
  }
  .contact-list svg { width: 14px; height: 14px; margin-right: 5px; fill: var(--orange); flex: none; }
  .address {
    position: absolute;
    top: 303px; left: 0; width: 100%;
    text-align: center;
    font-size: 16px;
    color: var(--ink);
  }
</style>
</head>
<body>

<section class="card card--front">
  <div class="brand-dot"></div>
  <div class="brand-name">Coral Pennant</div>
  <p class="website"><span class="website__domain">coralpennant</span>.com</p>
</section>

<section class="card card--back">
  <div class="back-band"></div>
  <div class="brand-dot"></div>
  <div class="brand-name">Coral Pennant</div>

  <h1 class="holder-name">DALE WHITCOMBE</h1>
  <div class="divider"></div>
  <ul class="contact-list">
    <li>
      <svg viewBox="0 0 24 24" aria-hidden="true"><path d="M6.6 10.8a15.1 15.1 0 0 0 6.6 6.6l2.2-2.2a1 1 0 0 1 1-.25 11.4 11.4 0 0 0 3.6.57 1 1 0 0 1 1 1V20a1 1 0 0 1-1 1A17 17 0 0 1 3 4a1 1 0 0 1 1-1h3.5a1 1 0 0 1 1 1c0 1.25.2 2.45.57 3.57a1 1 0 0 1-.25 1z"/></svg>
      555-731-8842
    </li>
    <li>
      <svg viewBox="0 0 24 24" aria-hidden="true"><path d="M6 2h12v5H6zM3 8h18a2 2 0 0 1 2 2v7h-4v5H5v-5H1v-7a2 2 0 0 1 2-2zm4 8v4h10v-4z"/></svg>
      555:731-8843
    </li>
    <li>
      <svg viewBox="0 0 24 24" aria-hidden="true"><path d="M7 1h10a2 2 0 0 1 2 2v18a2 2 0 0 1-2 2H7a2 2 0 0 1-2-2V3a2 2 0 0 1 2-2zm0 3v14h10V4zm5 15.2a1 1 0 1 0 0 2 1 1 0 0 0 0-2z"/></svg>
      555-382-1490
    </li>
    <li>
      <svg viewBox="0 0 24 24" aria-hidden="true"><path d="M2 4h20v16H2zm2 2v.5l8 5.5 8-5.5V6zm0 2.9V18h16V8.9l-8 5.5z"/></svg>
      dw@coralpennant.com
    </li>
  </ul>
  <p class="address">212 North Fenwick Lane, Seabrook Cove, FL 34112</p>
</section>

</body>
</html>
```